Corporate-Design für Steuerberatungsgesellschaft
Zielgruppe
Wir sind eine Steuerberatungsgesellschaft mit 10 Mitarbeitern im Norden von Deutschland, kurz vor der Ostseeküste. Unser Unternehmen besteht seit 30 Jahren. Wir betreuen vor allem Mandanten in kleinen und mittleren Unternehmen: von der Arztpraxis bis zum Bauunternehmen. Demnächst werden wir neue Räume beziehen. Diese sollen großzügiger und moderner werden, teilweise mit Glaswänden.
Aufgabenstellung
Unser bisheriges Farbkonzept war von bordeaux und creme geprägt (www.kanzlei-mervato.de). Das muss aber nicht weiter bestehen. Das bisherige Logo finden wir inhaltlich recht treffend, aber es sollte moderner gestaltet werden. Der Schriftzug des Kanzleinamens soll an der Fassade in silbernen Buchstaben angebracht werden.

```html
<!DOCTYPE html>
<html lang="de">
<head>
<meta charset="utf-8">
<title>Mervato Nord – Visitenkarte</title>
<link rel="stylesheet" href="https://fonts.googleapis.com/css2?family=Noto+Serif:wght@400;700&display=swap">
<style>
  :root {
    --backdrop: #6d6d71;
    --card-dark: #222123;
    --card-light: #ffffff;
    --bordeaux: #8b1629;
    --ink: #2a2a2a;
    --ink-soft: #555555;
    --rule: #333333;
    --on-dark: #f2f2f2;
  }
  * { box-sizing: border-box; margin: 0; padding: 0; }
  html, body {
    width: 1200px; height: 913px; overflow: hidden;
    background: var(--backdrop);
    font-family: "Noto Serif", Georgia, serif;
  }
  .sheet {
    width: 1200px; height: 913px;
    display: flex; align-items: center; justify-content: center; gap: 64px;
  }
  .card {
    width: 480px; height: 760px;
    position: relative;
    box-shadow: 0 14px 30px rgba(0,0,0,.35);
    text-align: center;
  }
  /* Rückseite */
  .card--back { background: var(--card-light); color: var(--ink); padding: 90px 48px 0; }
  .brand { display: inline-flex; align-items: center; gap: 12px; }
  .brand__square { width: 18px; height: 18px; background: var(--bordeaux); }
  .brand__name { font-size: 30px; font-weight: 700; letter-spacing: .04em; }
  .card--back .brand__name { color: var(--bordeaux); font-size: 24px; }
  .rule { height: 2px; background: var(--rule); margin: 36px 30px; }
  .person__degree { font-size: 15px; color: var(--ink-soft); }
  .person__name { font-size: 28px; font-weight: 700; color: var(--bordeaux); margin: 6px 0; }
  .person__role { font-size: 15px; color: var(--ink-soft); }
  .company { font-size: 16px; line-height: 1.55; }
  .company__name { color: var(--bordeaux); font-weight: 700; }
  .company__legal { font-weight: 700; }
  .contact { margin-top: 22px; font-size: 16px; line-height: 1.6; }
  .contact b { font-weight: 700; }
  /* Vorderseite */
  .card--front { background: var(--card-dark); color: var(--on-dark); }
  .card--front .brand { position: absolute; top: 330px; left: 0; right: 0; justify-content: center; }
  .card--front .brand__name { color: var(--on-dark); }
  .services {
    position: absolute; left: 0; right: 0; bottom: 110px;
    font-size: 16px; line-height: 1.7; letter-spacing: .02em;
  }
  .band { position: absolute; left: 0; right: 0; bottom: 0; height: 40px; background: var(--bordeaux); }
</style>
</head>
<body>
<main class="sheet">
  <section class="card card--back">
    <div class="brand"><span class="brand__square"></span><span class="brand__name">MERVATO NORD</span></div>
    <div class="rule"></div>
    <p class="person__degree">Diplom-Kaufmann</p>
    <p class="person__name">Jonas Brekeler</p>
    <p class="person__role">Geschäftsführer / Steuerberater</p>
    <div class="rule"></div>
    <div class="company">
      <p class="company__name">Mervato Nord</p>
      <p class="company__legal">Steuerberatungsgesellschaft mbH</p>
      <p>Lindenweg 12</p>
      <p>17000 Seestadt</p>
    </div>
    <div class="contact">
      <p><b>Fon</b> +49 (0) 3900 / 55 12 - 0</p>
      <p><b>Fax</b> +49 (0) 3900 / 55 12 - 14</p>
      <p>seestadt@kanzlei-mervato.de</p>
      <p>www.kanzlei-mervato.de</p>
    </div>
  </section>

  <section class="card card--front">
    <div class="brand"><span class="brand__square"></span><span class="brand__name">MERVATO NORD</span></div>
    <div class="services">
      <p>Steuerberatung / Finanz- und Lohnbuchhaltung</p>
      <p>Betriebswirtschaftliche Beratung</p>
    </div>
    <div class="band"></div>
  </section>
</main>
</body>
</html>
```